International business needs business cards

Our company, DRV Ventures Inc. is in the business of supplying a range construction products with particular emphasis on CEMENT. We have developed our own brand - TORVAN SUPPLIES - with which to infiltrate the market. We are launching our brand of cement (TORVAN Type IS Cement) into the Caribbean which is unlike anything this market has ever seen. A monopoly has existed here for the past 60-odd years and the market has now opened to allow the importation of other brands and consumers are anxious and ready for change/improvement. We are very excited to be launching and want to make a great first impression. We will be conducting workshops and seminars (from government level to the hardware store owners) and we want our business card to give us the strong, confident introduction that we need.

Target Market(s)

construction; builders; engineers; home owners

Industry/Entity Type

Construction

Contact Information for Business Card

Marisol Depree
CEO
cell # 1 555 4180736
Ground floor,Lindell Plaza Suite 2734
Port Selwyn,Grand Arvel
Arvel Islands,KY1-4823
EMAIL: m.depree@drvventuresinc.example
web site drvventuresinc.example

COMPANY: skype info drv.ventures.example

second card
Yvette Brannock-Depree
CFO
CELL# 1 555 607 3941
Port Selwyn,Grand Arvel
Arvel Islands,KY1-4823
EMAIL: y.brannockdepree@drvventuresinc.example
website drvventuresinc.example

Requirements
Must have
• Business cards must display BOTH logos - DRV is the company and TORVAN is the brand.

```html
<!DOCTYPE html>
<html lang="en">
<head>
<meta charset="utf-8">
<title>DRV Ventures Inc. – Business Card</title>
<link rel="stylesheet" href="https://fonts.googleapis.com/css2?family=Open+Sans:wght@400;600;700&display=swap">
<style>
  :root {
    --bg: #e6e6e6;
    --card-white: #ffffff;
    --card-black: #050505;
    --ink-dark: #2e2e2e;
    --ink-light: #ffffff;
    --accent-red: #8e1b1f;
    --divider: #8a8a8a;
  }
  * { margin: 0; padding: 0; box-sizing: border-box; }
  html, body {
    width: 1200px; height: 900px; overflow: hidden;
    background: var(--bg);
    font-family: "Open Sans", Arial, sans-serif;
  }
  .canvas { position: relative; width: 1200px; height: 900px; }
  .card {
    position: absolute; left: 250px; width: 700px; height: 400px;
    border-radius: 28px; overflow: hidden;
    box-shadow: 0 8px 24px rgba(0,0,0,0.18);
  }
  .card-front { top: 30px; background: var(--card-white); }
  .card-back { top: 470px; background: var(--card-black); color: var(--ink-light); }

  /* Front: brand mark */
  .brand-mark {
    position: absolute; left: 0; right: 0; top: 130px;
    display: flex; align-items: center; justify-content: center; gap: 16px;
  }
  .brand-dot { width: 30px; height: 30px; border-radius: 50%; background: var(--ink-dark); }
  .brand-name { font-size: 64px; font-weight: 700; color: var(--ink-dark); letter-spacing: 6px; }
  .brand-web {
    position: absolute; left: 0; right: 0; top: 318px;
    display: flex; align-items: center; justify-content: center; gap: 10px;
    font-size: 19px; font-weight: 600; color: var(--ink-dark);
  }
  .brand-web .web-dot { width: 18px; height: 18px; border-radius: 50%; background: var(--accent-red); }

  /* Back: company mark */
  .company-mark {
    position: absolute; left: 44px; top: 200px;
    display: flex; align-items: center; gap: 12px;
  }
  .company-square { width: 84px; height: 84px; background: var(--accent-red); flex: none; }
  .company-name {
    font-size: 24px; font-weight: 700; color: var(--ink-light); line-height: 1.15;
    width: 160px;
  }
  .divider {
    position: absolute; left: 312px; top: 96px; width: 1px; height: 236px;
    background: var(--divider);
  }
  .contact { position: absolute; left: 334px; top: 90px; right: 20px; }
  .contact-name { font-size: 30px; font-weight: 700; letter-spacing: 0.5px; line-height: 1.15; }
  .contact-title { font-size: 15px; font-weight: 600; margin-bottom: 10px; }
  .contact-address { font-size: 16px; font-weight: 600; line-height: 1.3; margin-bottom: 6px; }
  .contact-line {
    display: flex; align-items: center; gap: 8px;
    font-size: 16px; font-weight: 600; line-height: 1.4;
  }
  .contact-line svg { width: 13px; height: 13px; flex: none; }
</style>
</head>
<body>
<main class="canvas">
  <section class="card card-front" aria-label="Business card front">
    <div class="brand-mark">
      <span class="brand-dot"></span>
      <span class="brand-name">TORVAN</span>
    </div>
    <div class="brand-web">
      <span class="web-dot"></span>
      <span>drv.ventures.example</span>
    </div>
  </section>

  <section class="card card-back" aria-label="Business card back">
    <div class="company-mark">
      <span class="company-square"></span>
      <span class="company-name">DRV VENTURES<br>INC.</span>
    </div>
    <div class="divider"></div>
    <div class="contact">
      <div class="contact-name">MARISOL DEPREE</div>
      <div class="contact-title">CEO</div>
      <div class="contact-address">
        Ground floor,Lindell Plaza Suite 2734<br>
        Port Selwyn,Grand Arvel<br>
        Arvel Islands,KY1-4823
      </div>
      <div class="contact-line">
        <svg viewBox="0 0 16 16" aria-hidden="true"><path fill="#fff" d="M3 1l3 3-1.5 2a9 9 0 0 0 5.5 5.5L12 10l3 3-2 2C7 15 1 9 1 3z"/></svg>
        <span>1 555 4180736</span>
      </div>
      <div class="contact-line">
        <svg viewBox="0 0 16 16" aria-hidden="true"><rect x="1" y="3" width="14" height="10" fill="none" stroke="#fff" stroke-width="1.6"/><path d="M1 3l7 6 7-6" fill="none" stroke="#fff" stroke-width="1.6"/></svg>
        <span>m.depree@drvventuresinc.example</span>
      </div>
      <div class="contact-line">
        <svg viewBox="0 0 16 16" aria-hidden="true"><circle cx="8" cy="8" r="6.5" fill="none" stroke="#fff" stroke-width="1.4"/><ellipse cx="8" cy="8" rx="3" ry="6.5" fill="none" stroke="#fff" stroke-width="1.2"/><path d="M1.5 8h13" stroke="#fff" stroke-width="1.2"/></svg>
        <span>www.drvventuresinc.example</span>
      </div>
    </div>
  </section>
</main>
</body>
</html>
```